Website - Loretta Dubrow

I need a website that has multiple pages and easy for me to update pictures, content and blogs as an ongoing basis’s.
It will have videos and needs to be compatible to view easily and aesthetically on mobile phones.
Please refer to this website for inspiration www.quinnafernsby.com

Coding

Coded - Design and coding required

Number of Pages Required

5+ page

Other font styles liked:
• Refer to website provided as inspiration

Requirements
Must have
• Please use stock images for now to do design, but I will be providing all imagery, videos and content

```html
<!DOCTYPE html>
<html lang="en">
<head>
<meta charset="utf-8">
<title>Loretta Dubrow</title>
<link rel="stylesheet" href="https://fonts.googleapis.com/css2?family=Abril+Fatface&family=Lora:ital,wght@0,400;1,400&family=Roboto:wght@400&display=swap">
<style>
:root{
  --ink:#111111;
  --muted:#6f6f6f;
  --white:#ffffff;
  --ghost:#f3f3f3;
  --pink:#f4b6d6;
  --footer:#2a282a;
  --hero-a:#bdbdbd;
  --hero-b:#8f8f8f;
}
*{margin:0;padding:0;box-sizing:border-box}
html,body{width:1200px;height:2413px;overflow:hidden;background:var(--white)}
body{position:relative;font-family:'Lora',serif;color:var(--ink)}
.display{font-family:'Abril Fatface',serif;font-weight:400}
a{color:inherit;text-decoration:none}

.hero{position:absolute;left:0;top:0;width:1200px;height:639px;
  background:radial-gradient(ellipse at 50% 55%,#d0d0d0 0%,var(--hero-a) 40%,var(--hero-b) 100%)}
.hero-portrait{position:absolute;left:418px;top:200px;width:324px;height:439px;
  background:linear-gradient(180deg,#6a6a6a 0%,#3a3a3a 55%,#151515 100%);border-radius:150px 150px 0 0;opacity:.55}
.site-header{position:absolute;left:89px;right:93px;top:36px;display:flex;justify-content:space-between;align-items:center;color:var(--white)}
.brand{font-size:38px;letter-spacing:.5px}
.main-nav{display:flex;gap:59px;font-size:17px}
.play-btn{position:absolute;left:573px;top:293px}
.slide-arrow{position:absolute;top:308px}
.slide-arrow.prev{left:34px}.slide-arrow.next{left:1146px}

.about{position:absolute;left:0;top:639px;width:1200px;height:790px}
.about-media{position:absolute;left:89px;top:96px}
.about-ghost{position:absolute;left:465px;top:108px;font-size:118px;color:var(--ghost);line-height:1;white-space:nowrap}
.about-copy{position:absolute;left:693px;top:230px;width:416px}
.section-title{font-size:44px;line-height:1;margin-bottom:24px}
.about-copy p{font-size:15.5px;line-height:27px;color:var(--muted);text-align:justify;margin-bottom:9px}

.blog{position:absolute;left:0;top:1460px;width:1200px}
.blog-ghost{position:absolute;left:0;width:1200px;top:0;text-align:center;font-size:118px;color:var(--ghost);line-height:1}
.blog-title{position:absolute;left:0;width:1200px;top:86px;text-align:center;font-size:44px;line-height:1}
.post-grid{position:absolute;left:89px;top:151px;display:flex;gap:12px}
.post{width:333px}
.post-thumb{width:333px;height:349px}
.post h3{font-weight:400;font-style:italic;font-size:19px;line-height:24px;letter-spacing:.6px;margin-top:8px}
.post time{display:block;font-style:italic;font-size:14px;color:var(--muted);margin-top:9px;letter-spacing:.3px}

.site-footer{position:absolute;left:0;top:2136px;width:1200px;height:277px;background:var(--footer);color:var(--white);text-align:center}
.footer-brand{font-size:40px;margin-top:56px;line-height:1}
.footer-nav{display:flex;justify-content:center;gap:59px;font-size:17px;margin-top:20px}
.social{display:flex;justify-content:center;gap:26px;margin-top:54px}
.social span{width:15px;height:15px;border-radius:50%;background:var(--white)}
.copyright{font-family:'Roboto',sans-serif;font-size:12px;margin-top:22px}
</style>
</head>
<body>

<section class="hero">
  <div class="hero-portrait" role="img" aria-label="Black and white portrait of a woman with hands clasped"></div>
  <header class="site-header">
    <div class="brand display">Lorettadubrow</div>
    <nav class="main-nav"><a>Home</a><a>About Us</a><a>Blog</a><a>Contact Us</a></nav>
  </header>
  <svg class="slide-arrow prev" width="18" height="24" viewBox="0 0 18 24"><path d="M13 3 5 12l8 9" fill="none" stroke="#fff" stroke-width="2.5"/></svg>
  <svg class="play-btn" width="56" height="56" viewBox="0 0 56 56"><circle cx="28" cy="28" r="25.5" fill="none" stroke="#fff" stroke-width="3.5"/><path d="M22 17v22l18-11z" fill="#fff"/></svg>
  <svg class="slide-arrow next" width="18" height="24" viewBox="0 0 18 24"><path d="M5 3l8 9-8 9" fill="none" stroke="#fff" stroke-width="2.5"/></svg>
</section>

<section class="about">
  <div class="about-ghost display">About Us</div>
  <svg class="about-media" width="580" height="692" viewBox="0 0 580 692" role="img" aria-label="Two half-circle photos of a woman: in a pink dress on a jetty, and a smiling close-up portrait">
    <defs>
      <linearGradient id="lake" x1="0" y1="0" x2="0" y2="1"><stop offset="0" stop-color="#8ea3b8"/><stop offset=".5" stop-color="#c86fb3"/><stop offset="1" stop-color="#6d6a66"/></linearGradient>
      <linearGradient id="studio" x1="0" y1="0" x2="0" y2="1"><stop offset="0" stop-color="#e6e4e3"/><stop offset=".45" stop-color="#9a6b52"/><stop offset="1" stop-color="#ece8e4"/></linearGradient>
    </defs>
    <path d="M277 0 A285 285 0 0 0 277 570 Z" fill="url(#lake)"/>
    <path d="M281 118 A286 286 0 0 1 281 690 Z" fill="url(#studio)"/>
    <rect x="276" y="0" width="4" height="692" fill="#f4b6d6"/>
  </svg>
  <div class="about-copy">
    <h2 class="section-title display">About Us</h2>
    <p>Lorem ipsum dolor sit amet, consectetur adipiscing elit, sed do eiusmod tempor incididunt ut labore et dolore magna aliqua. Ut enim ad minim veniam, quis nostrud exercitation ullamco laboris nisi ut aliquip ex ea commodo consequat. Duis aute irure dolor in reprehenderit in voluptate velit esse cillum dolore eu fugiat nulla pariatur.</p>
    <p>Lorem ipsum dolor sit amet, consectetur adipiscing elit, sed do eiusmod tempor incididunt ut labore et dolore magna aliqua. Ut enim ad minim veniam, quis nostrud exercitation ullamco laboris nisi ut aliquip ex ea commodo consequat. Duis aute irure dolor in reprehenderit in voluptate velit esse cillum dolore eu fugiat nulla pariatur.</p>
  </div>
</section>

<section class="blog">
  <div class="blog-ghost display">Latest Blog</div>
  <h2 class="blog-title display">Latest Blog</h2>
  <div class="post-grid">
    <article class="post">
      <div class="post-thumb" role="img" aria-label="Woman sitting on a jetty by the water with skincare bottles" style="background:linear-gradient(180deg,#5f7a45 0%,#4d6a86 40%,#c9ccd8 75%,#7a6f66 100%)"></div>
      <h3>Lorem ipsum dolor sit amet, consectetur adipiscing</h3>
      <time>Jan 25,2021</time>
    </article>
    <article class="post">
      <div class="post-thumb" role="img" aria-label="Woman in green activewear and cap holding a tote bag" style="background:linear-gradient(180deg,#e9e9e7 0%,#b08a70 35%,#33402f 70%,#d6d5d2 100%)"></div>
      <h3>Lorem ipsum dolor sit amet, consectetur adipiscing</h3>
      <time>Jan 25,2021</time>
    </article>
    <article class="post">
      <div class="post-thumb" role="img" aria-label="Woman in a blue halter top by a white window" style="background:linear-gradient(180deg,#dfe3e6 0%,#8a5a3c 35%,#c99a7e 65%,#3454b8 100%)"></div>
      <h3>Lorem ipsum dolor sit amet, consectetur adipiscing</h3>
      <time>Jan 25,2021</time>
    </article>
  </div>
</section>

<footer class="site-footer">
  <div class="footer-brand display">Lorettadubrow</div>
  <nav class="footer-nav"><a>Home</a><a>About Us</a><a>Blog</a><a>Contact Us</a></nav>
  <div class="social" aria-label="Social links"><span></span><span></span><span></span><span></span></div>
  <p class="copyright">© Copyrights.2021.The Company Name.All Rights Reserved</p>
</footer>

</body>
</html>
```